Home Staging Company needs business card design

We're a home staging company called Brightly Settled Home Staging. We would like a business card design that includes aqua and gray. Our current logo of house within chair is fine but I find we almost always use the logo in one color. I'll upload images of front and back of our current card and our logo. Note that we have dropped "Solutions" from our company name and don't want to include it on the card.

Target Market(s)

Realtors and homeowners - people interested in selling their homes

Contact Information for Business Card

Marisol Thistlewood
Brightly Settled Home Staging
757-555-0193
www.brightlysettled.com
marisol@brightlysettled.com

Font styles to use
Serif
Script

Requirements
Must have
• My logo and contact details
• UPDATE***
• I forgot to say that the company name should be included on the front of the card somehow.

```html
<!DOCTYPE html>
<html lang="en">
<head>
<meta charset="utf-8">
<title>Brightly Settled Home Staging – Business Card</title>
<link rel="stylesheet" href="https://fonts.googleapis.com/css2?family=Libre+Baskerville:wght@400;700&family=Open+Sans:wght@400;600&display=swap">
<style>
  :root {
    --aqua: #3abcc7;
    --aqua-light: #5fd0d8;
    --charcoal: #444444;
    --charcoal-dark: #3b3b3b;
    --backdrop: #262626;
    --white: #ffffff;
    --serif: "Libre Baskerville", Georgia, serif;
    --sans: "Open Sans", Arial, sans-serif;
  }
  * { box-sizing: border-box; margin: 0; padding: 0; }
  html, body { width: 1200px; height: 900px; overflow: hidden; background: var(--backdrop); }
  .canvas { position: relative; width: 1200px; height: 900px; }

  .card {
    position: absolute;
    width: 700px;
    height: 400px;
    overflow: hidden;
    box-shadow: 0 14px 30px rgba(0,0,0,.45);
  }
  .card-front { left: 60px; top: 50px; background: var(--charcoal); }
  .card-back  { left: 440px; top: 460px; background: var(--charcoal-dark); }
  .card-shapes { position: absolute; inset: 0; }

  /* Front */
  .holder { position: absolute; right: 60px; top: 70px; text-align: right; color: var(--white); }
  .holder-name { font-family: var(--serif); font-size: 24px; font-variant: small-caps; letter-spacing: 1px; }
  .holder-role { font-family: var(--sans); font-size: 11px; margin-top: 2px; }

  .contact-list { position: absolute; right: 40px; top: 165px; list-style: none; text-align: right; }
  .contact-item {
    display: flex; align-items: center; justify-content: flex-end; gap: 10px;
    font-family: var(--serif); font-size: 13px; color: var(--white); height: 26px;
  }
  .contact-item .icon { width: 18px; height: 18px; }
  .contact-item.no-icon { padding-right: 28px; }

  .brand { position: absolute; }
  .brand-front { left: 70px; top: 175px; }
  .brand-name { font-family: var(--serif); font-weight: 400; font-size: 34px; line-height: 1.1; }
  .brand-tag { font-family: var(--serif); font-size: 13px; letter-spacing: 2px; text-transform: uppercase; margin-top: 6px; }
  .brand-front .brand-name { color: var(--aqua); }
  .brand-front .brand-tag { color: var(--white); padding-left: 70px; }

  .web-link {
    position: absolute; display: flex; align-items: center; gap: 10px;
    font-family: var(--serif); font-size: 16px; color: var(--white);
  }
  .web-link .icon { width: 20px; height: 20px; }
  .card-front .web-link { left: 290px; top: 330px; }

  /* Back */
  .brand-back { left: 0; right: 0; top: 120px; text-align: center; color: var(--white); }
  .brand-back .brand-name { font-size: 42px; }
  .brand-back .brand-tag { font-size: 17px; text-transform: none; letter-spacing: 1px; margin-top: 10px; }
  .card-back .web-link { left: 0; right: 0; top: 290px; justify-content: center; font-size: 17px; }
</style>
</head>
<body>
<main class="canvas">

  <section class="card card-front" aria-label="Front of card">
    <svg class="card-shapes" viewBox="0 0 700 400" aria-hidden="true">
      <line x1="0" y1="300" x2="700" y2="300" stroke="var(--aqua)" stroke-width="1.5"/>
      <path d="M230 300 Q250 300 258 318 L262 330 Q268 345 290 345 L620 345 Q640 345 645 325 L650 300 Z" fill="var(--aqua)"/>
      <path d="M230 300 Q250 300 258 318 L262 330 Q268 345 290 345 L620 345 Q640 345 645 325 L650 300" fill="none" stroke="var(--aqua)" stroke-width="1"/>
    </svg>

    <div class="holder">
      <p class="holder-name">Marisol Thistlewood</p>
      <p class="holder-role">Designation</p>
    </div>

    <ul class="contact-list">
      <li class="contact-item">757-555-0193
        <svg class="icon" viewBox="0 0 20 20" aria-hidden="true"><circle cx="10" cy="10" r="9" fill="none" stroke="var(--aqua)" stroke-width="1.5"/><path d="M6.5 6 L8 5.5 L9 8 L8 9 Q9 11 11 12 L12 11 L14.5 12 L14 13.5 Q10 14 6.5 10 Z" fill="var(--aqua)"/></svg>
      </li>
      <li class="contact-item">www.brightlysettled.com
        <svg class="icon" viewBox="0 0 20 20" aria-hidden="true"><circle cx="10" cy="10" r="9" fill="none" stroke="var(--aqua)" stroke-width="1.5"/><rect x="5.5" y="7" width="9" height="6.5" fill="var(--aqua)"/><path d="M5.5 7 L10 10.5 L14.5 7" fill="none" stroke="var(--charcoal)" stroke-width="1"/></svg>
      </li>
      <li class="contact-item no-icon">marisol@brightlysettled.com</li>
    </ul>

    <div class="brand brand-front">
      <p class="brand-name">Brightly Settled</p>
      <p class="brand-tag">Home Staging</p>
    </div>

    <p class="web-link">
      <svg class="icon" viewBox="0 0 20 20" aria-hidden="true"><circle cx="10" cy="10" r="8.5" fill="none" stroke="var(--white)" stroke-width="1.5"/><ellipse cx="10" cy="10" rx="3.5" ry="8.5" fill="none" stroke="var(--white)" stroke-width="1"/><line x1="1.5" y1="10" x2="18.5" y2="10" stroke="var(--white)" stroke-width="1"/></svg>
      www.brightlysettled.com
    </p>
  </section>

  <section class="card card-back" aria-label="Back of card">
    <svg class="card-shapes" viewBox="0 0 700 400" aria-hidden="true">
      <path d="M0 0 H700 V270 L590 270 Q570 270 566 290 L562 315 Q558 340 535 340 L190 340 Q168 340 160 322 L150 300 Q145 285 125 285 L0 285 Z" fill="var(--aqua)"/>
    </svg>

    <div class="brand brand-back">
      <p class="brand-name">Brightly Settled</p>
      <p class="brand-tag">Home Staging</p>
    </div>

    <p class="web-link">
      <svg class="icon" viewBox="0 0 20 20" aria-hidden="true"><circle cx="10" cy="10" r="8.5" fill="none" stroke="var(--white)" stroke-width="1.5"/><ellipse cx="10" cy="10" rx="3.5" ry="8.5" fill="none" stroke="var(--white)" stroke-width="1"/><line x1="1.5" y1="10" x2="18.5" y2="10" stroke="var(--white)" stroke-width="1"/></svg>
      www.brightlysettled.com
    </p>
  </section>

</main>
</body>
</html>
```